Professional violinist needs business cards

I am trying to attract the following jobs:
-private violin lessons (primarily classical)
-performance gigs (weddings, birthday parties, funerals, etc.)
-collaborations with other artists (studio recordings, performances)

I want to communicate that I have a very high standard of excellence for my work, but I also love people and celebrations.
Values/style words I like are:
love, joy, peace, fun, beauty, authenticity, excellence, warmth, refined/sleek, free spirited. If that's too confusing, just ignore :)

I will attach my favorite business card template that I could find on Canva. The lines are supposed to be like a music staff, which I think is really cool, but I also don't want it to look too busy. I like the simple black and white--I think it looks sharp--but I also am open to other ideas. I also have seen business cards with pictures included that looked great, so I attached an image that could be used as well.

I am also attaching a file that I made of my initials that could be used as a logo, but I'm not sure if it should be included.

Information on the card:
-My name (18 letters total)
-"violinist"
-phone number, email, website

Thank you!

```html
<!DOCTYPE html>
<html lang="en">
<head>
<meta charset="UTF-8">
<title>Lena Marwood – Violinist Business Cards</title>
<link rel="stylesheet" href="https://fonts.googleapis.com/css2?family=Raleway:wght@500;600&family=Arimo:wght@400&display=swap">
<style>
  :root {
    --stage: #2a2a2a;
    --card: #050505;
    --card-sheen: #1c1c1c;
    --gold: #d29f3a;
    --white: #f4f4f4;
    --photo-dark: #0d0a09;
    --photo-warm: #4a2c1e;
  }
  * { margin: 0; padding: 0; box-sizing: border-box; }
  html, body {
    width: 1200px; height: 900px; overflow: hidden;
    background: var(--stage);
  }
  .canvas {
    position: relative; width: 1200px; height: 900px;
  }
  .card {
    position: absolute; left: 250px; width: 700px; height: 400px;
    background: var(--card); overflow: hidden;
  }
  .card--front { top: 40px; }
  .card--back {
    top: 460px;
    background: linear-gradient(100deg, var(--card) 0%, var(--card) 55%, var(--card-sheen) 100%);
  }

  /* Front: music staff */
  .staff { position: absolute; inset: 0; }
  .brand-name {
    position: absolute; left: 40px; top: 146px;
    padding: 6px 18px;
    background: var(--card);
    font-family: "Raleway", sans-serif; font-weight: 600;
    font-size: 64px; line-height: 1; color: var(--gold);
    letter-spacing: 1px;
  }
  .front-web {
    position: absolute; right: 30px; bottom: 98px;
    font-family: "Arimo", sans-serif; font-size: 15px;
    color: var(--white); letter-spacing: 1px;
  }

  /* Back: portrait and details */
  .portrait {
    position: absolute; left: 40px; top: 0; width: 250px; height: 400px;
    background: radial-gradient(ellipse at 50% 30%, var(--photo-warm) 0%, var(--photo-dark) 70%);
  }
  .details {
    position: absolute; left: 350px; top: 190px;
  }
  .details__name {
    font-family: "Raleway", sans-serif; font-weight: 500;
    font-size: 34px; color: var(--gold); letter-spacing: 1px; line-height: 1;
  }
  .details__role {
    font-family: "Raleway", sans-serif; font-weight: 500;
    font-size: 16px; color: var(--white); margin-top: 4px;
  }
  .contact { list-style: none; margin-top: 36px; }
  .contact__item {
    display: flex; align-items: center; gap: 16px;
    font-family: "Arimo", sans-serif; font-size: 19px;
    color: var(--white); height: 30px;
  }
  .contact__icon { width: 18px; height: 18px; flex: none; }
</style>
</head>
<body>
<main class="canvas">

  <section class="card card--front">
    <svg class="staff" width="700" height="400" viewBox="0 0 700 400" aria-hidden="true">
      <g stroke="var(--gold)" stroke-width="5">
        <line x1="0" y1="80" x2="700" y2="80"/>
        <line x1="0" y1="140" x2="700" y2="140"/>
        <line x1="0" y1="200" x2="700" y2="200"/>
        <line x1="0" y1="260" x2="700" y2="260"/>
        <line x1="0" y1="320" x2="700" y2="320"/>
      </g>
    </svg>
    <div class="brand-name">Lena Marwood</div>
    <div class="front-web">www.lenamarwood.com</div>
  </section>

  <section class="card card--back">
    <div class="portrait" role="img" aria-label="Portrait of the violinist in a black dress holding her violin and bow"></div>
    <div class="details">
      <h1 class="details__name">Lena Marwood</h1>
      <p class="details__role">Violinist</p>
      <ul class="contact">
        <li class="contact__item">
          <svg class="contact__icon" viewBox="0 0 18 18" aria-hidden="true">
            <path d="M2 6 Q9 1 16 6 L14 8 L11 6 L7 6 L4 8 Z" fill="var(--gold)"/>
            <rect x="4" y="9" width="10" height="7" rx="1.5" fill="var(--gold)"/>
          </svg>
          <span>020 4417 3860</span>
        </li>
        <li class="contact__item">
          <svg class="contact__icon" viewBox="0 0 18 18" aria-hidden="true">
            <rect x="1.5" y="4" width="15" height="10" fill="none" stroke="var(--gold)" stroke-width="2"/>
            <path d="M1.5 4 L9 10 L16.5 4" fill="none" stroke="var(--gold)" stroke-width="2"/>
          </svg>
          <span>hello@lenamarwood.com</span>
        </li>
        <li class="contact__item">
          <svg class="contact__icon" viewBox="0 0 18 18" aria-hidden="true">
            <circle cx="9" cy="9" r="7.5" fill="none" stroke="var(--gold)" stroke-width="2"/>
            <ellipse cx="9" cy="9" rx="3" ry="7.5" fill="none" stroke="var(--gold)" stroke-width="1.5"/>
            <line x1="1.5" y1="9" x2="16.5" y2="9" stroke="var(--gold)" stroke-width="1.5"/>
          </svg>
          <span>www.lenamarwood.com</span>
        </li>
      </ul>
    </div>
  </section>

</main>
</body>
</html>
```